UK Online Auction Site needs a clever design

We need a contemporary landing page and registration page design for a UK auction website, that look equally at home on PC's and tablets . The design should be fresh, bright, clean, professional, robust, and familiar. We would like to see something clever but functional.

Online

```html
<!DOCTYPE html>
<html lang="en">
<head>
<meta charset="utf-8">
<title>Lotmark – Online Auctions</title>
<link href="https://fonts.googleapis.com/css2?family=Open+Sans:wght@400;600;700&family=Raleway:wght@300;400&family=Yanone+Kaffeesatz:wght@400;500&family=Tinos&display=swap" rel="stylesheet">
<style>
:root{
  --blue:#1482cf;
  --blue-dark:#0f6fb4;
  --blue-light:#2496e0;
  --top-grey:#ebebeb;
  --text:#555;
  --muted:#888;
  --dark:#1f1f1f;
  --darker:#171717;
  --btn-grey:#4a4a4a;
  --line:#e2e2e2;
}
*{box-sizing:border-box;margin:0;padding:0}
html,body{width:778px;height:1200px;overflow:hidden;background:#fff}
body{position:relative;font-family:"Open Sans",sans-serif;color:var(--text)}
.abs{position:absolute}

.top-bar{left:0;top:0;width:778px;height:30px;background:var(--top-grey);font-family:"Tinos",serif;font-size:10px;color:#666}
.top-bar .welcome{left:66px;top:8px}
.top-bar .links{right:70px;top:8px;display:flex;gap:18px}
.top-bar .links span{display:flex;align-items:center;gap:5px}
.top-bar svg{fill:#bbb}

.brand{left:66px;top:52px;width:170px;height:44px;display:flex;align-items:center;gap:8px;font-size:26px;font-weight:700;color:var(--blue);white-space:nowrap}
.brand i{flex:none;width:12px;height:12px;background:var(--blue);border-radius:50%;display:block}
.search{left:463px;top:63px;width:205px;height:20px;background:var(--blue);color:#fff;font-size:8px;padding:5px 8px}
.search .go{position:absolute;right:0;top:0;width:22px;height:20px;background:#0a4e84;display:flex;align-items:center;justify-content:center}
.cart{left:676px;top:55px;width:37px;height:34px;background:#eee;border-radius:2px;display:flex;align-items:center;justify-content:center}

.main-nav{left:0;top:117px;width:778px;height:39px;background:linear-gradient(var(--blue-light),var(--blue-dark));display:flex;padding-left:63px;font-size:10px;color:#fff}
.main-nav div{height:39px;display:flex;align-items:center;justify-content:center;gap:5px;border-right:1px solid rgba(0,0,0,.12)}
.main-nav .cat{width:149px;background:var(--blue-dark)}
.main-nav svg{fill:#fff}

.hero-title{left:67px;top:224px;font-size:20px;font-weight:400;color:var(--blue);letter-spacing:.3px}
.hero-copy{left:67px;top:266px;width:256px;font-size:9.2px;line-height:13px;color:#666;text-align:justify}
.btn-view{left:124px;top:376px;width:81px;height:25px;background:var(--blue);color:#fff;font-size:9px;display:flex;align-items:center;justify-content:center}
.hero-img{left:428px;top:260px;width:230px;height:100px;background:linear-gradient(100deg,#2a2a2a 0 60%,#3d5a7a 60% 100%);border-radius:8px}

.feature{top:480px;width:215px;height:75px}
.feature .icon{position:absolute;left:2px;top:4px;width:56px;height:64px;border-radius:6px}
.feature h3{position:absolute;left:67px;top:7px;font-size:10.5px;font-weight:700;color:var(--blue);letter-spacing:.3px;white-space:nowrap}
.feature p{position:absolute;left:68px;top:30px;width:140px;font-size:6.3px;line-height:12px;font-weight:600;color:#666;text-transform:uppercase}

.products-head{left:63px;top:626px;width:657px;height:20px}
.products-head .rule{position:absolute;left:20px;right:20px;top:9px;border-top:1px solid var(--line)}
.arrow{position:absolute;top:0;width:17px;height:17px;border-radius:50%;display:flex;align-items:center;justify-content:center}
.products-head .ribbon{position:absolute;left:262px;top:-2px;width:141px;height:26px;background:var(--blue);color:#fff;font-family:"Yanone Kaffeesatz",sans-serif;font-size:14px;letter-spacing:.8px;display:flex;align-items:center;justify-content:center}

.card{top:686px;width:151px;height:213px}
.card.active{border:1px solid #e6e6e6;box-shadow:0 0 6px rgba(0,0,0,.06)}
.card .photo{position:absolute;left:24px;top:14px;width:104px;height:120px;border-radius:4px}
.card .rule{position:absolute;left:0;right:0;top:150px;border-top:1px solid #e6e6e6}
.card .name{position:absolute;left:10px;top:150px;font-family:"Yanone Kaffeesatz",sans-serif;font-size:15px;color:#333;line-height:18px;padding-top:3px}
.card .price{position:absolute;left:10px;top:178px;font-family:"Yanone Kaffeesatz",sans-serif;font-size:19px;color:#777}
.card .add{position:absolute;right:10px;top:178px;width:62px;height:22px;border-radius:2px;background:var(--btn-grey);color:#fff;font-family:"Yanone Kaffeesatz",sans-serif;font-size:13.5px;display:flex;align-items:center;justify-content:center}
.card.active .add{background:var(--blue)}

.footer{left:0;top:954px;width:778px;height:210px;background:var(--dark);color:#888}
.footer .notch{position:absolute;right:88px;top:0;border:6px solid transparent;border-top-color:#fff}
.footer h4{position:absolute;top:33px;font-family:"Raleway",sans-serif;font-weight:300;font-size:20px;color:#fff}
.footer p{position:absolute;font-size:8px;line-height:12px;color:#7d7d7d}
.footer .email{position:absolute;left:68px;top:117px;width:144px;height:19px;background:#2c2c2c;font-size:8px;color:#999;padding:4px 6px}
.footer .sub{position:absolute;left:140px;top:147px;width:72px;height:20px;background:var(--blue);color:#fff;font-size:9.5px;display:flex;align-items:center;justify-content:center}
.footer .when{color:#bbb}
.fb-box{position:absolute;left:418px;top:67px;width:126px;height:118px;background:#fff;padding:5px 6px;color:#333;font-size:6px}
.fb-box .sq{display:inline-block;width:11px;height:11px;background:var(--blue);vertical-align:middle;margin-right:3px}
.fb-box .grid{display:grid;grid-template-columns:repeat(4,26px);gap:3px;margin-top:6px}
.fb-box .grid div{height:26px;background:#b9bec6}

.bottom-bar{left:0;top:1164px;width:778px;height:36px;background:var(--darker)}
.social{position:absolute;top:0;width:37px;height:36px;display:flex;align-items:center;justify-content:center;border-right:1px solid #2a2a2a}
.social i{display:block;width:14px;height:14px;border-radius:50%;background:#4a4a4a}
.social.on{background:var(--blue)}
.social.on i{background:#fff}
.copy{position:absolute;right:63px;top:12px;font-size:9px;color:#ddd}
</style>
</head>
<body>

<div class="abs top-bar">
  <span class="abs welcome">Welcome to our site</span>
  <div class="abs links">
    <span><svg width="10" height="10" viewBox="0 0 10 10"><circle cx="5" cy="3" r="2.5"/><path d="M0 10c0-3 2-4.5 5-4.5s5 1.5 5 4.5z"/></svg>Login</span>
    <span><svg width="8" height="10" viewBox="0 0 8 10"><rect y="4" width="8" height="6"/><path d="M2 4V3a2 2 0 014 0v1" fill="none" stroke="#bbb" stroke-width="1.2"/></svg>Create an Account</span>
  </div>
</div>

<div class="abs brand"><i></i>Lotmark</div>
<div class="abs search">Search item here
  <span class="go"><svg width="9" height="9" viewBox="0 0 10 10"><circle cx="4" cy="4" r="3" fill="none" stroke="#fff" stroke-width="1.4"/><path d="M6.2 6.2L9 9" stroke="#fff" stroke-width="1.6"/></svg></span>
</div>
<div class="abs cart"><svg width="16" height="14" viewBox="0 0 16 14"><path d="M1 1h2.5l2 8h8l1.5-6H4.5" fill="none" stroke="#666" stroke-width="1.2"/><circle cx="6.5" cy="12" r="1.2" fill="#666"/><circle cx="12.5" cy="12" r="1.2" fill="#666"/></svg></div>

<nav class="abs main-nav">
  <div class="cat">Shop By Categories <svg width="8" height="6" viewBox="0 0 8 6"><path d="M0 0h8L4 6z"/></svg></div>
  <div style="width:80px"><svg width="9" height="9" viewBox="0 0 9 9"><rect width="9" height="6" rx="1"/><rect x="2" y="7" width="5" height="2"/></svg>Sell</div>
  <div style="width:98px"><svg width="8" height="9" viewBox="0 0 8 9"><rect y="4" width="8" height="5"/><path d="M2 4V3a2 2 0 014 0v1" fill="none" stroke="#fff" stroke-width="1.2"/></svg>Sign In</div>
  <div style="width:103px"><svg width="11" height="9" viewBox="0 0 11 9"><path d="M0 1h2l1.5 5h6l1-4H3"/><circle cx="4" cy="8" r="1"/><circle cx="9" cy="8" r="1"/></svg>Basket</div>
  <div style="width:91px">? Help</div>
  <div style="width:98px;border-right:0"><svg width="7" height="9" viewBox="0 0 7 9"><path d="M2 0L0 1.5c0 3 2 6 5 7.5L7 7.5 5 5.5 4 6.5C3 5.5 2.5 4.5 2.3 3.3L3.5 2.5z"/></svg>Contact</div>
</nav>

<h1 class="abs hero-title">Shop Cameras</h1>
<p class="abs hero-copy">Long established fact that a reader will be distracted by the readable content of a page when looking at its layout. The point of using Lorem Ipsum is that it has a more-or-less normal distribution of letters, as opposed to using 'Content here, content here', making it look like readable English. Many desktop publishing packages and web page editors now use</p>
<div class="abs btn-view">VIEW NOW</div>
<div class="abs hero-img" role="img" aria-label="Compact digital camera beside its flip-out touch screen"></div>

<div class="abs feature" style="left:63px">
  <div class="icon" role="img" aria-label="Security badge illustration" style="background:linear-gradient(#d7dde4,#aab4bf)"></div>
  <h3>COMPLETELY SAFE</h3>
  <p>Bid on or buy items you're watching or searching for</p>
</div>
<div class="abs feature" style="left:282px">
  <div class="icon" role="img" aria-label="Gold trophy illustration" style="background:linear-gradient(#f0cd6a,#d2a23a)"></div>
  <h3>PREMIUM SELLERS</h3>
  <p>Great service and the best delivery when you buy from premium sellers.</p>
</div>
<div class="abs feature" style="left:508px">
  <div class="icon" role="img" aria-label="Gold rating star illustration" style="background:linear-gradient(#f5cf6a,#e3aa2c)"></div>
  <h3>FEEDBACK RATING SYSTEM</h3>
  <p>View seller history and feedback of users before you bid or buy.</p>
</div>

<div class="abs products-head">
  <div class="rule"></div>
  <div class="arrow" style="left:0;background:var(--blue)"><svg width="7" height="9" viewBox="0 0 7 9"><path d="M5.5 1L2 4.5 5.5 8" fill="none" stroke="#fff" stroke-width="1.8"/></svg></div>
  <div class="arrow" style="right:0;background:#e4e4e4"><svg width="7" height="9" viewBox="0 0 7 9"><path d="M1.5 1L5 4.5 1.5 8" fill="none" stroke="#fff" stroke-width="1.8"/></svg></div>
  <div class="ribbon">OUR PRODUCTS</div>
</div>

<div class="abs card active" style="left:66px">
  <div class="photo" role="img" aria-label="Floor lamp with orange shade on a tripod stand" style="background:linear-gradient(#f3e1d8,#e9e9e9)"></div>
  <div class="name">Lorem ipsum</div>
  <div class="price">$35.99</div>
  <div class="add">Add to Cart</div>
</div>
<div class="abs card" style="left:232px">
  <div class="photo" role="img" aria-label="Colourful retro toy camera" style="background:linear-gradient(135deg,#8fd8d4,#e7dc86);top:40px;height:80px"></div>
  <div class="rule"></div>
  <div class="name">Lorem ipsum</div>
  <div class="price">$35.99</div>
  <div class="add">Add to Cart</div>
</div>
<div class="abs card" style="left:397px">
  <div class="photo" role="img" aria-label="Black digital SLR camera" style="background:linear-gradient(#3a3a3a,#111);top:26px;height:94px"></div>
  <div class="rule"></div>
  <div class="name">Lorem ipsum</div>
  <div class="price">$35.99</div>
  <div class="add">Add to Cart</div>
</div>
<div class="abs card" style="left:562px">
  <div class="photo" role="img" aria-label="Table lamp with warm amber shade" style="background:linear-gradient(#f7cf92,#ececec)"></div>
  <div class="rule"></div>
  <div class="name">Lorem ipsum</div>
  <div class="price">$35.99</div>
  <div class="add">Add to Cart</div>
</div>

<footer class="abs footer">
  <span class="notch"></span>
  <h4 style="left:68px">Newsletter</h4>
  <p style="left:68px;top:80px;width:140px">Subscribe to be the first to know about Sales, Events, and Exclusive Offers!</p>
  <div class="email">Enter Your Email</div>
  <div class="sub">Subscribe</div>

  <h4 style="left:245px">Contact</h4>
  <p style="left:245px;top:80px;width:150px">lorem ipsum street ,2 New York City, NY, United States</p>
  <p style="left:245px;top:115px">(020) 7946-0312<br>(020) 7946-0847</p>
  <p style="left:245px;top:145px">info@lotmark.co.uk<br>help@lotmark.co.uk</p>

  <h4 style="left:419px">Friendbook</h4>
  <div class="fb-box">
    <div style="font-weight:700;color:#3b5998"><span class="sq"></span>Friendbook</div>
    <div style="margin:2px 0 0 14px;border:1px solid #ccc;width:26px;padding:0 2px">Like</div>
    <div style="margin-top:6px">87,092,159 people like Friendbook.</div>
    <div class="grid"><div></div><div></div><div></div><div></div><div></div><div></div><div></div><div></div></div>
  </div>

  <h4 style="left:577px">Chirper</h4>
  <p style="left:577px;top:80px;width:140px">Viking - Premium lorem ipsum lotm.kr/8Hq2Zx #lorem<br><span class="when">about 9 hours ago</span></p>
  <p style="left:577px;top:128px;width:140px">Modus - Premium ipsum dolor lotm.kr/8Hq2Zx #lorem<br><span class="when">about 12 hours ago</span></p>
</footer>

<div class="abs bottom-bar">
  <div class="social on" style="left:68px"><i></i></div>
  <div class="social" style="left:105px"><i></i></div>
  <div class="social" style="left:142px"><i></i></div>
  <div class="social" style="left:179px"><i></i></div>
  <div class="social" style="left:216px"><i></i></div>
  <div class="copy">Copyrights © 2014 Marrowvale - All rights reserved.</div>
</div>

</body>
</html>
```